Rovelux

Hi everyone!

Looks like our project is more sophisticated than we expected. So good news - we increased the budget! and one of you will sure get the prize - no money back for us!

We are a young Russian company that specializes in in-taxi entertainment. We believe that our key strength is great attention to user experience. We've devoted much effort to improve ergonomics of our devices - tablet PCs that we install in the taxis. And yes, we enjoy to simplify things!

Now we need the most basic things - a logo and some staff for client meetings (primarily advertisers and ad agencies).

As for logo - we already have one engraved on the prototypes of our device (see attached file). This is one of the ideas (still far from perfect) - what we appreciate in it is minimalistic yet stylish approach.

As for "take it to the meeting stuff" we want to start with name card, pen and notepad (A4) that we will leave in clients's office, also as a reminder. Shall your have more smart ideas - always welcome!

As for logo and name cards - we would like to make an image of serious but modern company. Our design should communicate creativity and reliability. We believe that "to understand is to simplify" - minimalistic design is the most difficult one. Its better to work hard on fonts and arrangement, than put 10 variegated images.

SO THE TASK IS TO DESIGN:
- a logo
- a name card
- a note pad (great example in attachment)
- a pen

Shall you have more questions - please ask in comments.

We look forward to meeting like-minded fellows here!
Updates

Target Market(s)

Out target are:

- advertiser
- advertising agencies
- taxi passenger

Industry/Entity Type

It Company

Requirements
Must have
• font should be chosen very carefully
Nice to have
• classic minimalistic plain text only but very stylish name card is a dream of one of our co-founders:)
Should not have
• we do not want to have taxi-like colors and chess-boards. We are closer to "innovation", "entertainment", and "user experience", rather than "taxi".

```html
<!DOCTYPE html>
<html lang="en">
<head>
<meta charset="utf-8">
<title>Rovelux — Name Card Options</title>
<link rel="stylesheet" href="https://fonts.googleapis.com/css2?family=Questrial&display=swap">
<style>
  :root {
    --ink: #231f20;
    --accent: #f7941d;
    --paper: #ffffff;
    --backdrop: #d3dde3;
    --rule: #8a8a8a;
    --shadow: rgba(40, 55, 65, 0.28);
  }
  * { margin: 0; padding: 0; box-sizing: border-box; }
  html, body { width: 1200px; height: 1000px; overflow: hidden; }
  body {
    position: relative;
    font-family: "Questrial", "Century Gothic", sans-serif;
    color: var(--ink);
    background: var(--backdrop);
  }
  .brand-header {
    position: absolute; left: 0; top: 0;
    width: 1200px; height: 233px;
    background: var(--paper);
  }
  .wordmark {
    position: absolute;
    display: flex; align-items: center; gap: 10px;
    line-height: 1; white-space: nowrap;
  }
  .wordmark .name { letter-spacing: -0.01em; }
  .wordmark .dot {
    border-radius: 50%; background: var(--accent); flex: none;
  }
  .wordmark--light {
    left: 150px; top: 80px; font-size: 88px;
  }
  .wordmark--light .dot { width: 22px; height: 22px; }
  .wordmark-panel {
    position: absolute; left: 633px; top: 59px;
    width: 433px; height: 123px; background: var(--ink);
  }
  .wordmark--dark {
    left: 38px; top: 18px; font-size: 88px; color: var(--paper);
  }
  .wordmark--dark .dot { width: 22px; height: 22px; }

  .option-number {
    position: absolute; font-size: 24px; color: var(--ink);
  }
  .card {
    position: absolute; width: 457px; height: 254px;
    background: var(--paper);
    box-shadow: 0 2px 8px var(--shadow);
  }
  .card .wordmark { font-size: 46px; gap: 6px; }
  .card .wordmark .dot { width: 11px; height: 11px; }
  .holder { position: absolute; line-height: 1.15; }
  .holder .person { font-size: 19.5px; letter-spacing: 0.02em; }
  .holder .role { font-size: 14px; }
  .divider {
    position: absolute; height: 1px; background: var(--rule);
  }
  .contacts {
    position: absolute; font-size: 12.5px; line-height: 15.5px;
    list-style: none; white-space: nowrap;
  }
  .contacts .sep { color: var(--accent); padding: 0 2px; }
  .contacts--marked li::before {
    content: "•"; color: var(--accent); margin-right: 4px; font-size: 10px;
  }
  .contacts--centered .sep { color: var(--ink); }
</style>
</head>
<body>

<header class="brand-header">
  <div class="wordmark wordmark--light"><span class="name">Rovelux</span><span class="dot"></span></div>
  <div class="wordmark-panel">
    <div class="wordmark wordmark--dark"><span class="name">Rovelux</span><span class="dot"></span></div>
  </div>
</header>

<!-- Option 1 -->
<span class="option-number" style="left:36px;top:326px;">1</span>
<section class="card" style="left:86px;top:321px;">
  <div class="wordmark" style="right:28px;top:30px;"><span class="name">Rovelux</span><span class="dot"></span></div>
  <div class="holder" style="left:0;width:644px;top:104px;text-align:center;">
    <div class="person">Mikhail Orlov</div>
    <div class="role">General Manager</div>
  </div>
  <ul class="contacts contacts--marked" style="left:16px;top:193px;">
    <li>Moscow, Ulitsa Lesnaya, 12</li>
    <li>tel: +495 218 47 309 <span class="sep">•</span> mob: +495 761 530 288</li>
    <li>rovelux.com <span class="sep">•</span> e-mail: rovelux@mailbox.com</li>
  </ul>
</section>

<!-- Option 2 -->
<span class="option-number" style="left:600px;top:326px;">2</span>
<section class="card" style="left:650px;top:321px;">
  <div class="wordmark" style="right:28px;top:30px;"><span class="name">Rovelux</span><span class="dot"></span></div>
  <div class="holder" style="left:0;width:610px;top:113px;text-align:center;">
    <div class="person">Mikhail Orlov</div>
    <div class="role">General Manager</div>
  </div>
  <div class="divider" style="left:18px;width:418px;top:185px;"></div>
  <ul class="contacts contacts--marked" style="left:16px;top:193px;">
    <li>Moscow, Ulitsa Lesnaya, 12</li>
    <li>tel: +495 218 47 309 <span class="sep">•</span> mob: +495 761 530 288</li>
    <li>rovelux.com <span class="sep">•</span> e-mail: rovelux@mailbox.com</li>
  </ul>
</section>

<!-- Option 3 -->
<span class="option-number" style="left:36px;top:662px;">3</span>
<section class="card" style="left:86px;top:657px;">
  <div class="wordmark" style="left:0;right:0;top:34px;justify-content:center;"><span class="name">Rovelux</span><span class="dot"></span></div>
  <div class="holder" style="left:0;width:457px;top:124px;text-align:center;">
    <div class="person">Mikhail Orlov</div>
    <div class="role">General Manager</div>
  </div>
  <div class="divider" style="left:117px;width:226px;top:185px;"></div>
  <ul class="contacts contacts--centered" style="left:0;width:457px;top:193px;text-align:center;">
    <li>Moscow, Ulitsa Lesnaya, 12</li>
    <li>tel: +495 218 47 309 <span class="sep">•</span> mob: +495 761 530 288</li>
    <li>rovelux.com <span class="sep">•</span> e-mail: rovelux@mailbox.com</li>
  </ul>
</section>

<!-- Option 4 -->
<span class="option-number" style="left:600px;top:662px;">4</span>
<section class="card" style="left:650px;top:657px;">
  <div class="wordmark" style="left:28px;top:22px;"><span class="name">Rovelux</span><span class="dot"></span></div>
  <div class="holder" style="left:28px;top:111px;">
    <div class="person">Mikhail Orlov</div>
    <div class="role">General Manager</div>
  </div>
  <div class="divider" style="left:28px;width:408px;top:185px;"></div>
  <ul class="contacts contacts--marked" style="left:26px;top:193px;">
    <li>Moscow, Ulitsa Lesnaya, 12</li>
    <li>tel: +495 218 47 309 <span class="sep">•</span> mob: +495 761 530 288</li>
    <li>rovelux.com <span class="sep">•</span> e-mail: rovelux@mailbox.com</li>
  </ul>
</section>

</body>
</html>
```